Provide bookkeeping and accounting services to small and growing businesses

We need website and logo design using the name Dornaby as the logo.
The target audience are small companies and startups who need:
1) Simple bookkeeping services
2) Accounting advice that only someone with many years of senior financial experience as a CPA can provide.

The services are provided by two individuals. each of whom specialize in one of the areas.

We want the website to be clean without a lot of visual distraction but don't know how to make a boring subject interesting. We believe our potential clients, small business owners, need to find what they want quickly and easily without a lot of verbiage or distractions.

We've attached a draft of the homepage and have completed the text on most of the other pages.

Target Market(s)

small and early stage growth companies in San Diego North County

Industry/Entity Type

Accounting

Number of Pages Required

1 page

Font styles to use
Sans Serif

Colors
86cfc6
33b8a4
85cae6

Requirements
Must have
• We need a design for the website homepage that includes the name Dornaby as the logo. Must include a design for the name.
• Must have color in teal or greenish blue.
Nice to have
• White background, clean, clear, uncluttered.
• We would like to use the design in a Theme on a WordPress website. Themes Paper Lantern and Quiet Harbour are appealing to us.
Should not have
• Moving pictures

```html
<!DOCTYPE html>
<html lang="en">
<head>
<meta charset="utf-8">
<title>Dornaby Accounting and Bookkeeping</title>
<link rel="stylesheet" href="https://fonts.googleapis.com/css2?family=Ubuntu:wght@400;500;700&family=Lato:wght@400;700&display=swap">
<style>
:root{
  --teal:#33b8a4;
  --teal-band:#3bbba6;
  --mint:#86cfc6;
  --mint-dark:#6cc3b9;
  --sky:#85cae6;
  --ink:#222;
  --text:#333;
  --muted:#777;
  --rule:#d8d8d8;
  --footer:#1b1b1b;
  --white:#fff;
}
*{box-sizing:border-box;margin:0;padding:0}
html,body{width:1200px;height:2344px;overflow:hidden}
body{position:relative;background:var(--white);font-family:"Lato",sans-serif;color:var(--text)}
.abs{position:absolute}
.heading{font-family:"Ubuntu",sans-serif;font-weight:400}

/* header */
.site-header{position:absolute;left:0;top:0;width:1200px;height:103px}
.brand-name{position:absolute;left:102px;top:6px;font-family:"Ubuntu",sans-serif;font-size:48px;color:var(--teal);line-height:1}
.brand-tag{position:absolute;left:101px;top:63px;font-size:17px;color:var(--ink)}
.contact-chip{position:absolute;top:26px;display:flex;align-items:center;gap:10px;font-size:15px;color:var(--ink);line-height:1.3}
.contact-chip svg{flex:none}

/* nav */
.main-nav{position:absolute;left:0;top:103px;width:1200px;height:41px;background:var(--mint)}
.nav-item{position:absolute;top:0;height:41px;line-height:41px;text-align:center;color:var(--white);font-size:16px;border-right:1px solid rgba(255,255,255,.35)}
.nav-item.active{background:var(--mint-dark)}

/* hero */
.hero{position:absolute;left:0;top:144px;width:1200px;height:541px;background:linear-gradient(100deg,#e4e8e6 0%,#f2f3f1 40%,#dfe3e6 62%,#eceeef 100%)}
.hero-title{position:absolute;left:102px;top:196px;font-family:"Ubuntu",sans-serif;font-weight:700;font-size:39px;line-height:52px;color:var(--white);text-shadow:0 1px 6px rgba(0,0,0,.35)}
.hero-dots{position:absolute;left:575px;top:507px;display:flex;gap:6px}
.hero-dots span{width:12px;height:12px;border-radius:50%;background:var(--teal)}
.hero-dots span.hollow{background:var(--white);border:2px solid var(--teal)}

/* section headings */
.section-title{position:absolute;left:0;width:1200px;text-align:center;font-size:34px;color:var(--ink)}
.section-title em{font-style:normal;color:var(--teal)}
.title-rule{position:absolute;left:419px;width:362px;height:8px}
.title-rule::before{content:"";position:absolute;left:0;right:0;top:3px;height:2px;background:var(--rule)}
.title-rule::after{content:"";position:absolute;left:177px;top:0;width:8px;height:8px;border-radius:50%;background:#bbb}

/* welcome */
.welcome-copy{position:absolute;left:102px;top:803px;width:994px;text-align:center;font-size:13.6px;line-height:24px;color:var(--text)}
.btn{position:absolute;display:flex;align-items:center;justify-content:center;gap:8px;color:var(--white);font-size:13px;text-transform:uppercase}
.btn .arrow{width:20px;height:20px;border-radius:50%;background:var(--white);display:flex;align-items:center;justify-content:center}
.btn-sky{background:var(--sky);border:1px solid #a9d9ee}

/* services */
.services{position:absolute;left:0;top:1008px;width:1200px;height:406px;background:var(--teal-band)}
.services-title{position:absolute;left:102px;top:36px;font-size:34px;color:var(--white)}
.services-rule{position:absolute;left:309px;top:57px;width:425px;height:1px;background:rgba(255,255,255,.6)}
.service-icon{position:absolute;width:128px;height:128px;border-radius:50%;background:rgba(255,255,255,.3);display:flex;align-items:center;justify-content:center}
.service-name{position:absolute;font-size:19px;font-weight:700;color:var(--white)}
.service-text{position:absolute;width:290px;font-size:14px;line-height:21px;color:var(--white)}
.btn-outline{position:absolute;width:94px;height:34px;line-height:32px;text-align:center;font-size:14px;color:var(--white);border:1px solid rgba(255,255,255,.8);background:rgba(255,255,255,.2)}

/* inquiry */
.inquiry{position:absolute;left:795px;top:1047px;width:305px;height:331px;background:var(--white);box-shadow:0 2px 8px rgba(0,0,0,.15)}
.inquiry-tab{position:absolute;left:809px;top:1039px;width:278px;height:42px;background:var(--sky);color:var(--white);font-family:"Ubuntu",sans-serif;font-size:24px;text-align:center;line-height:42px}
.field{position:absolute;left:24px;width:264px;border:1px solid #e2e2e2;background:linear-gradient(#fff,#f4f4f4);display:flex;font-size:14px;color:#444}
.field .ico{width:38px;border-right:1px solid #e2e2e2;display:flex;justify-content:center;padding-top:10px}
.field .label{padding:9px 0 0 10px}

/* reviews */
.review-avatar{position:absolute;width:84px;height:84px;border-radius:50%;border:3px solid #ccc;background:linear-gradient(#cfd6d8,#9aa6a8)}
.review-text{position:absolute;width:364px;font-size:15px;line-height:23px;color:var(--ink);text-indent:38px}
.quote-open,.quote-close{position:absolute;font-family:"Ubuntu",sans-serif;font-weight:700;font-size:40px;color:#c9d3dc;line-height:1}
.review-name{position:absolute;font-size:16px;font-weight:700;color:var(--teal)}
.review-divider{position:absolute;left:598px;top:1555px;width:1px;height:130px;background:#e5e5e5}

/* call to action */
.cta{position:absolute;left:0;top:1767px;width:1200px;height:281px;background:linear-gradient(180deg,#7fc3e4 0%,#86c9e6 55%,#a7d6ec 100%)}
.cta-text{position:absolute;left:100px;top:54px;width:1000px;text-align:center;font-family:"Ubuntu",sans-serif;font-size:33px;line-height:45px;color:var(--white)}
.btn-teal{background:var(--teal);text-transform:none;font-size:17px}

/* footer */
.site-footer{position:absolute;left:0;top:2048px;width:1200px;height:252px;background:var(--footer);color:var(--white)}
.footer-heading{position:absolute;top:34px;font-size:16px;padding-bottom:10px;border-bottom:1px dashed #555}
.footer-links{position:absolute;left:102px;top:73px;list-style:none;font-size:12px;line-height:24px}
.footer-links li::before{content:"›";margin-right:10px;color:#aaa}
.col-sep{position:absolute;top:34px;width:1px;height:190px;background:#2e2e2e}
.contact-row{position:absolute;left:292px;display:flex;gap:12px;font-size:12px;line-height:19px;font-weight:700}
.map{position:absolute;left:581px;top:74px;width:257px;height:136px;background:linear-gradient(135deg,#ecebe5,#dcdbd2);border:2px solid #777}
.footer-brand{position:absolute;left:922px;top:92px;width:172px;text-align:center}
.footer-brand .name{font-family:"Ubuntu",sans-serif;font-size:40px;color:#ccc;line-height:1}
.footer-brand .tag{font-size:12px;color:#bbb;margin-top:6px}
.social{position:absolute;top:170px;width:24px;height:24px;border-radius:50%}
.copyright{position:absolute;left:0;top:2300px;width:1200px;height:44px;background:var(--teal);color:var(--white);font-size:13px;text-align:center;line-height:44px}
</style>
</head>
<body>

<header class="site-header">
  <div class="brand-name">Dornaby</div>
  <div class="brand-tag">Accounting and Bookkeeping</div>
  <div class="contact-chip" style="left:750px">
    <svg width="38" height="44" viewBox="0 0 38 44"><circle cx="18" cy="22" r="16" fill="none" stroke="#33b8a4" stroke-width="2"/><path d="M11 12c-3 3 0 12 6 18 5 5 10 6 12 4l-4-5-3 2c-3-2-6-6-7-9l3-2z" fill="#33b8a4"/></svg>
    <div>Call Us:<br>(012) 555 0147</div>
  </div>
  <div class="contact-chip" style="left:911px">
    <svg width="40" height="44" viewBox="0 0 40 44"><path d="M3 16 L30 6 L37 30 L10 40 Z" fill="none" stroke="#33b8a4" stroke-width="2.5"/><path d="M3 16 L22 26 L30 6" fill="none" stroke="#33b8a4" stroke-width="2.5"/></svg>
    <div>Mail Us:<br>info@dornaby.com</div>
  </div>
</header>

<nav class="main-nav">
  <div class="nav-item active" style="left:98px;width:149px">Home</div>
  <div class="nav-item" style="left:247px;width:175px">About Us</div>
  <div class="nav-item" style="left:422px;width:168px">Services</div>
  <div class="nav-item" style="left:590px;width:186px">Experience</div>
  <div class="nav-item" style="left:776px;width:134px;border-right:none">Resources</div>
  <div class="nav-item" style="left:910px;width:188px;border-left:1px solid rgba(255,255,255,.35)">Contact Us</div>
</nav>

<section class="hero" role="img" aria-label="Photo of a smiling accountant in shirt and tie with colleagues meeting in a bright office">
  <h1 class="hero-title">Providing a full range of<br>accounting, tax, bookkeeping<br>and business consulting services</h1>
  <div class="hero-dots"><span></span><span class="hollow"></span><span></span></div>
</section>

<h2 class="section-title heading" style="top:726px">Welcome To <em>Dornaby</em> Accounting and Bookkeeping</h2>
<div class="title-rule" style="top:777px"></div>
<p class="welcome-copy">Lorem ipsum dolouar sit amet consec tetuer adipiscing elnit. Praebulum molesbeutie lacus. Aenea nonuendrerit maurihasellu porta. Fusce suscpvarius mi. Cum sociis natoque penatibus et magnis dis parturientontes nascetur ridiculus mus. Nulla dui. Fusce feugiat mal esuada odio. Morbi nunc odio gravida atcursus necuctus a lorem. Maecenas tristique orci ac sem uis ultricies pharetra magna. Donec accumsan malesuada orci.onec sit amet eros. Lorem ipsu m dolor sit amet consectetuer adipiscing elit. Mauris fermentum dictum reet aliquam leo tellus dolor dapibus eget elementum vel cursus eleifend elit.</p>
<div class="btn btn-sky" style="left:539px;top:923px;width:119px;height:35px">Read More <span class="arrow"><svg width="10" height="10" viewBox="0 0 10 10"><path d="M3 1l4 4-4 4" fill="none" stroke="#85cae6" stroke-width="2"/></svg></span></div>

<section class="services">
  <h2 class="services-title heading">Our Services</h2>
  <div class="services-rule"></div>

  <div class="service-icon" style="left:116px;top:105px">
    <svg width="72" height="80" viewBox="0 0 72 80" fill="none" stroke="#fff" stroke-width="3"><rect x="28" y="14" width="34" height="54" rx="3"/><rect x="34" y="20" width="22" height="10"/><g fill="#fff" stroke="none"><rect x="34" y="36" width="6" height="6"/><rect x="44" y="36" width="6" height="6"/><rect x="34" y="46" width="6" height="6"/><rect x="44" y="46" width="6" height="6"/><rect x="34" y="56" width="6" height="6"/><rect x="44" y="56" width="6" height="6"/></g><path d="M24 14c-8-4-16 0-14 6s14 5 14 12-10 8-16 4M16 8v34"/></svg>
  </div>
  <div class="service-icon" style="left:480px;top:105px">
    <svg width="64" height="76" viewBox="0 0 64 76" fill="none" stroke="#fff" stroke-width="3"><path d="M18 6h30l10 10v54H18z"/><path d="M10 14v56h40"/><path d="M36 30c-4-3-10-1-9 3s10 3 10 8-7 6-11 3M32 26v24"/><path d="M42 32h10M42 40h10M42 48h10M24 58h28"/></svg>
  </div>

  <svg class="abs" style="left:290px;top:1px" width="160" height="220" viewBox="0 0 160 220"><path d="M83 100v108M6 207h148" stroke="#fff" stroke-width="2"/><path d="M4 207l9-6v12zM156 207l-9-6v12z" fill="#fff"/></svg>

  <div class="service-name" style="left:98px;top:248px">Simple bookkeeping</div>
  <p class="service-text" style="left:98px;top:277px">Lorem ipsum dolouar sit amet consec tetuerrt scing elnit. Praebulum molesbeutie lacus.</p>
  <div class="btn-outline" style="left:98px;top:333px">Read More</div>

  <div class="service-name" style="left:471px;top:248px">Accounting advice</div>
  <p class="service-text" style="left:471px;top:277px">Lorem ipsum dolouar sit amet consec tetuerrt scing elnit. Praebulum molesbeutie lacus.</p>
  <div class="btn-outline" style="left:472px;top:333px">Read More</div>
</section>

<form class="inquiry">
  <div class="field" style="top:47px;height:33px"><span class="ico"><svg width="12" height="12" viewBox="0 0 12 12"><circle cx="6" cy="3.5" r="3" fill="#999"/><path d="M0 12c0-4 3-5 6-5s6 1 6 5z" fill="#999"/></svg></span><span class="label">Name</span></div>
  <div class="field" style="top:90px;height:35px"><span class="ico"><svg width="12" height="12" viewBox="0 0 12 12"><path d="M2 1l3 3-1.5 1.5c1 2 2 3 3 3L8 7l3 3-2 2C5 12 0 7 0 3z" fill="#999"/></svg></span><span class="label">Phone</span></div>
  <div class="field" style="top:133px;height:34px"><span class="ico"><svg width="13" height="10" viewBox="0 0 13 10"><rect x=".5" y=".5" width="12" height="9" fill="none" stroke="#999"/><path d="M.5 .5l6 5 6-5" fill="none" stroke="#999"/></svg></span><span class="label">Email</span></div>
  <div class="field" style="top:178px;height:84px"><span class="ico"><svg width="12" height="12" viewBox="0 0 12 12"><rect x=".5" y="2.5" width="9" height="9" fill="none" stroke="#999"/><path d="M5 7l6-6" stroke="#999" stroke-width="1.5"/></svg></span><span class="label">Message</span></div>
  <div class="btn btn-sky" style="left:24px;top:281px;width:120px;height:34px">Read More <span class="arrow"><svg width="10" height="10" viewBox="0 0 10 10"><path d="M3 1l4 4-4 4" fill="none" stroke="#85cae6" stroke-width="2"/></svg></span></div>
</form>
<div class="inquiry-tab">Quick Inquiry</div>

<h2 class="section-title heading" style="top:1456px">Customer <em>Reviews</em></h2>
<div class="title-rule" style="top:1506px"></div>

<svg class="abs" style="left:55px;top:1591px" width="20" height="38" viewBox="0 0 20 38"><path d="M18 2L3 19l15 17" fill="none" stroke="#aaa" stroke-width="2"/></svg>
<svg class="abs" style="left:1125px;top:1591px" width="20" height="38" viewBox="0 0 20 38"><path d="M2 2l15 17L2 36" fill="none" stroke="#aaa" stroke-width="2"/></svg>

<div class="review-avatar" style="left:100px;top:1570px" role="img" aria-label="Portrait of reviewer Jenisto"></div>
<span class="quote-open" style="left:203px;top:1552px">“</span>
<p class="review-text" style="left:203px;top:1553px">Lorem ipsum dolor sit amet, onsectietuer icingr eliterei sed diam nonummy nibh euismod tincideuntr ut laoreet dolore gna roerererweire aliquam eraterer lutpatei. Uti wisi enim ad miwinim veniam, quiserere istrud wer rreri tation.</p>
<span class="quote-close" style="left:365px;top:1646px">”</span>
<div class="review-name" style="left:203px;top:1679px">- Jenisto</div>

<div class="review-divider"></div>

<div class="review-avatar" style="left:630px;top:1570px" role="img" aria-label="Portrait of reviewer Vinoud"></div>
<span class="quote-open" style="left:734px;top:1552px">“</span>
<p class="review-text" style="left:734px;top:1553px">Lorem ipsum dolor sit amet, onsectietuer icingr eliterei sed diam nonummy nibh euismod tincideuntr ut laoreet dolore gna roerererweire aliquam eraterer lutpatei. Uti wisi enim ad miwinim veniam, quiserere istrud wer rreri tation.</p>
<span class="quote-close" style="left:895px;top:1646px">”</span>
<div class="review-name" style="left:734px;top:1679px">- Vinoud</div>

<section class="cta" role="img" aria-label="Soft blue photo of a businessman in a suit against a hazy mountain backdrop">
  <p class="cta-text">Dornaby offers a flexible range of accounting and bookkeeping services and support for small and growing organizations in San Diego North County.</p>
  <div class="btn btn-teal" style="left:530px;top:199px;width:139px;height:37px">Call Us Today <span class="arrow"><svg width="10" height="10" viewBox="0 0 10 10"><path d="M3 1l4 4-4 4" fill="none" stroke="#33b8a4" stroke-width="2"/></svg></span></div>
</section>

<footer class="site-footer">
  <div class="footer-heading" style="left:102px;width:110px">Quick Links</div>
  <ul class="footer-links">
    <li>Home</li><li>About Us</li><li>Services</li><li>Experience</li><li>Resources</li><li>Contact Us</li>
  </ul>
  <div class="col-sep" style="left:248px"></div>

  <div class="footer-heading" style="left:292px;width:208px">Contact Information</div>
  <div class="contact-row" style="top:79px"><svg width="12" height="16" viewBox="0 0 12 16"><path d="M6 0a6 6 0 016 6c0 4-6 10-6 10S0 10 0 6a6 6 0 016-6z" fill="#33b8a4"/><circle cx="6" cy="6" r="2.2" fill="#1b1b1b"/></svg><span>DORNABY<br>123 euismod cidun ut laoreet<br>laoreet dol magna aliquam</span></div>
  <div class="contact-row" style="top:151px"><svg width="12" height="14" viewBox="0 0 12 12"><path d="M2 1l3 3-1.5 1.5c1 2 2 3 3 3L8 7l3 3-2 2C5 12 0 7 0 3z" fill="#33b8a4"/></svg><span>(012) 555 0147</span></div>
  <div class="contact-row" style="top:189px;font-weight:400"><svg width="13" height="14" viewBox="0 0 13 10"><rect width="13" height="10" fill="#33b8a4"/><path d="M0 0l6.5 5L13 0" fill="none" stroke="#1b1b1b"/></svg><span>info@dornaby.com</span></div>
  <div class="col-sep" style="left:537px"></div>

  <div class="footer-heading" style="left:580px;width:250px">Location Map</div>
  <div class="map" role="img" aria-label="Street map showing the office location"></div>
  <div class="col-sep" style="left:877px"></div>

  <div class="footer-brand"><div class="name">Dornaby</div><div class="tag">Accounting and Bookkeeping</div></div>
  <span class="social" style="left:946px;background:#3b5998" aria-label="Social profile"></span>
  <span class="social" style="left:977px;background:#1e7bb8" aria-label="Social profile"></span>
  <span class="social" style="left:1011px;background:#1da1e2" aria-label="Social profile"></span>
  <span class="social" style="left:1046px;background:#dd4b39" aria-label="Social profile"></span>
</footer>
<div class="copyright">Copyright © 2016 Dornaby Accounting and Bookkeeping. All Rights Reserved.</div>

</body>
</html>
```